Tavel Website

Need a 4 page Drupal website - Home, About Us, Portfolio, Contact for a private equity/venture capital firm and new logo - company name is Tavel Corporation. The design should communicate - stock markets, hedge funds, deal-making, investments. The Portfolio section is to showcase the small companies we invest in. Hoping for something fresh, dynamic, even fun - no cliche financial images of New York. Not technical - but know how use Drupal content management to make text edits, blocks, articles, etc. We don't use any social media - so no chirply, Pagebook or WorkNode links. We need space for a post heron email sign-up form. Need website uploaded to my Corvane web hosting account. First time user of Sketch Plaza - have 3 other company websites that need refreshing.

```html
<!DOCTYPE html>
<html lang="en">
<head>
<meta charset="utf-8">
<title>Tavel Corporation</title>
<link href="https://fonts.googleapis.com/css2?family=Roboto+Condensed:wght@400;700&family=Ubuntu:wght@500&family=Arimo:wght@400;700&display=swap" rel="stylesheet">
<style>
:root{
  --green:#7cc24d;
  --green-dark:#5a9e2f;
  --ink:#2f3238;
  --text:#6e6e6e;
  --muted:#8a8a8a;
  --line:#e3e3e3;
  --footer:#33363f;
  --white:#fff;
}
*{margin:0;padding:0;box-sizing:border-box}
html,body{width:786px;height:1200px;overflow:hidden;background:var(--white)}
body{position:relative;font-family:"Arimo",Arial,sans-serif;color:var(--text)}
.abs{position:absolute}
.top-rule{left:0;top:0;width:786px;height:2px;background:#3a3d44}

/* header */
.brand{left:86px;top:20px;display:flex;align-items:center;gap:7px}
.brand-dot{width:24px;height:24px;border-radius:50%;background:var(--green)}
.brand-name{font-family:"Roboto Condensed",sans-serif;font-weight:700;font-size:17px;color:var(--ink);letter-spacing:.2px}
.nav{right:86px;top:28px;display:flex;gap:22px;font-family:"Roboto Condensed",sans-serif;font-size:9.5px;color:#444}
.nav .active{color:var(--green)}

/* hero */
.hero-photo{left:86px;top:58px;width:423px;height:238px;background:linear-gradient(120deg,#dfe4ea 0%,#c9d1da 35%,#b59a6a 70%,#8a7550 100%)}
.slide-btn{top:268px;width:16px;height:16px;background:rgba(60,60,60,.75);display:flex;align-items:center;justify-content:center}
.signup{left:509px;top:58px;width:191px;height:238px;background:var(--green);text-align:center;color:var(--white)}
.signup h2{font-family:"Roboto Condensed",sans-serif;font-weight:700;font-size:15px;margin-top:25px;letter-spacing:.2px}
.signup p{font-size:7px;line-height:13px;margin:9px 14px 0}
.field{position:absolute;left:14px;width:165px;height:25px;border:1px solid #e9f5df;font-size:7px;text-align:left;padding:8px 9px;color:#eef8e6}
.subscribe{position:absolute;left:43px;top:187px;width:109px;height:25px;border:1px solid #e9f5df;background:var(--green-dark);font-size:8px;line-height:23px}

/* sections */
.title{left:0;width:786px;text-align:center;font-family:"Roboto Condensed",sans-serif;font-weight:700;font-size:15px;color:var(--ink)}
.title span{color:var(--green);font-weight:400}
.lead{left:120px;width:546px;text-align:center;font-size:7px;line-height:15px;color:var(--muted)}
.welcome-text{left:130px;width:526px;text-align:center;font-size:7px;line-height:16px;color:var(--text)}
.rule{left:86px;width:615px;height:1px;background:var(--line)}

/* services */
.service-art{width:66px;height:80px;border-radius:4px}
.service-title{position:absolute;font-family:"Ubuntu",sans-serif;font-weight:500;font-size:11.5px;color:var(--ink)}
.service-text{position:absolute;width:214px;font-size:6.3px;line-height:14px;color:var(--text)}

/* portfolio */
.client{top:794px;width:109px;height:85px;border:1px solid #e6e6e6;box-shadow:0 0 2px rgba(0,0,0,.06);display:flex;align-items:center;justify-content:center;font-family:"Arimo",sans-serif;font-weight:700;font-size:15px;color:#2c5c8f}
.arrow{width:20px;height:20px;border-radius:50%;background:#a9a9a9;display:flex;align-items:center;justify-content:center}
.arrow.small{width:13px;height:13px;background:#8e8e8e}

/* news */
.news-photo{width:114px;height:108px}
.news-kicker{position:absolute;font-weight:400;font-size:8px;color:var(--green)}
.news-sub{position:absolute;font-weight:400;font-size:7px;color:#333}
.news-text{position:absolute;width:165px;font-size:6.6px;line-height:13.5px;color:var(--muted)}
.more{position:absolute;width:60px;height:22px;background:var(--green);color:var(--white);font-weight:700;font-size:8px;text-align:center;line-height:22px}
.vdiv{left:392px;top:996px;width:1px;height:112px;background:var(--line)}

/* footer */
.footer{left:0;top:1138px;width:786px;height:62px;background:var(--footer);color:var(--white);font-size:7.5px}
.footer-links{position:absolute;left:87px;top:27px;display:flex;gap:9px}
.footer-links .sep{color:#bbb}
.copyright{position:absolute;right:86px;top:27px;font-size:7px}
</style>
</head>
<body>
<div class="abs top-rule"></div>

<header>
  <div class="abs brand"><div class="brand-dot"></div><div class="brand-name">TAVEL CORPORATION</div></div>
  <nav class="abs nav"><span class="active">HOME</span><span>ABOUT US</span><span>PORTFOLIO</span><span>CONTACT</span></nav>
</header>

<section>
  <div class="abs hero-photo" role="img" aria-label="Photo of a hand placing a coin on stacks of coins"></div>
  <div class="abs slide-btn" style="left:100px"><svg width="6" height="8" viewBox="0 0 6 8"><path d="M5 0L1 4l4 4" fill="none" stroke="#fff" stroke-width="1.4"/></svg></div>
  <div class="abs slide-btn" style="left:120px"><svg width="6" height="8" viewBox="0 0 6 8"><path d="M1 0l4 4-4 4" fill="none" stroke="#fff" stroke-width="1.4"/></svg></div>
  <div class="abs signup">
    <h2>NEWSLETTER SIGNUP</h2>
    <p>Sed ut perspiciatis unde omnis iste natus error sit voluptatem accusantium doloremque laudantium, beatae vitae dicta sunt explicabo</p>
    <div class="field" style="top:106px">Enter Your Email :</div>
    <div class="field" style="top:144px">Enter Your Password :</div>
    <div class="subscribe">SUBSCRIBE</div>
  </div>
</section>

<section>
  <h1 class="abs title" style="top:313px">WELCOME TO <span>TAVEL COPORATION</span></h1>
  <p class="abs welcome-text" style="top:342px">Sed ut perspiciatis unde omnis iste natus error sit voluptatem accusantium doloremque laudantium, totam rem aperiam, eaque ipsa quae ab illo inventore veritatis et quasi architecto beatae vitae dicta sunt explicaboSed ut perspiciatis unde omnis iste natus error sit voluptatem accusantium doloremque laudan-tium, totam rem aperiam, eaque ipsa quae ab illo inventore veritatis et quasi architecto beatae vitae dicta sunt explicabo</p>
  <div class="abs rule" style="top:408px"></div>
</section>

<section>
  <h2 class="abs title" style="top:421px">OUR <span>SERVICES</span></h2>
  <p class="abs lead" style="top:445px">At Meridian Works we have the requisite skills in web application development to build robust, agile, and enterprise class applications. We have mastered the most widely used software technologies including Stratum Commerce, Velora .</p>

  <div class="abs service-art" role="img" aria-label="Laptop showing a pie chart" style="left:86px;top:496px;background:linear-gradient(#5aa7e0,#c9ccd0)"></div>
  <h3 class="service-title" style="left:166px;top:498px">STOCK MARKETS</h3>
  <p class="service-text" style="left:167px;top:517px">At Meridian Works we have the requisite skills in web application development to build robust, agile, and enterprise class applloinologies including Stratum Commerce, Velora .</p>

  <div class="abs service-art" role="img" aria-label="Rising green chart over stacks of gold coins" style="left:410px;top:490px;background:linear-gradient(#9fd66a,#e2b23c)"></div>
  <h3 class="service-title" style="left:490px;top:498px">HEDGE FUNDS</h3>
  <p class="service-text" style="left:491px;top:517px">At Meridian Works we have the requisite skills in web application development to build robust, agile, and enterprise class applloinologies including Stratum Commerce, Velora .</p>

  <div class="abs service-art" role="img" aria-label="Globe circled by red arrows" style="left:86px;top:602px;background:radial-gradient(circle,#4d9de0 30%,#f0b545 55%,#e5e5e5 80%)"></div>
  <h3 class="service-title" style="left:166px;top:602px">DEAL-MAKING</h3>
  <p class="service-text" style="left:167px;top:621px">At Meridian Works we have the requisite skills in web application development to build robust, agile, and enterprise class applloinologies including Stratum Commerce, Velora .</p>

  <div class="abs service-art" role="img" aria-label="Pink piggy bank with a coin" style="left:410px;top:598px;background:radial-gradient(circle,#f5a98e 40%,#fbe3d9 75%,#fff 90%)"></div>
  <h3 class="service-title" style="left:490px;top:602px">INVESTMENTS.</h3>
  <p class="service-text" style="left:491px;top:621px">At Meridian Works we have the requisite skills in web application development to build robust, agile, and enterprise class applloinologies including Stratum Commerce, Velora .</p>

  <div class="abs rule" style="top:705px"></div>
</section>

<section>
  <h2 class="abs title" style="top:723px">LATEST <span>PORTFOLIO</span></h2>
  <p class="abs lead" style="top:747px">At Meridian Works we have the requisite skills in web application development to build robust, agile, and enterprise class applications. We have mastered the most widely used software technologies including Stratum Commerce, Velora .</p>
  <div class="abs arrow" style="left:77px;top:827px"><svg width="8" height="10" viewBox="0 0 8 10"><path d="M6 1L2 5l4 4" fill="none" stroke="#fff" stroke-width="2"/></svg></div>
  <div class="abs client" style="left:95px">Northvale</div>
  <div class="abs client" style="left:217px;color:#263a7a">Quillion</div>
  <div class="abs client" style="left:339px;color:#333">LumenSight</div>
  <div class="abs client" style="left:461px;color:#1f3fbf">Halden</div>
  <div class="abs client" style="left:581px;color:#333;font-weight:400;letter-spacing:2px">KESTREL</div>
  <div class="abs arrow" style="left:688px;top:827px"><svg width="8" height="10" viewBox="0 0 8 10"><path d="M2 1l4 4-4 4" fill="none" stroke="#fff" stroke-width="2"/></svg></div>
</section>

<section>
  <div class="abs arrow small" style="left:324px;top:916px"><svg width="6" height="7" viewBox="0 0 6 7"><path d="M4.5 1L2 3.5 4.5 6" fill="none" stroke="#fff" stroke-width="1.5"/></svg></div>
  <h2 class="abs title" style="top:913px">RECENT <span>NEWS</span></h2>
  <div class="abs arrow small" style="left:449px;top:916px"><svg width="6" height="7" viewBox="0 0 6 7"><path d="M1.5 1L4 3.5 1.5 6" fill="none" stroke="#fff" stroke-width="1.5"/></svg></div>
  <p class="abs lead" style="top:939px">At Meridian Works we have the requisite skills in web application development to build robust, agile, and enterprise class applications. We have mastered the most widely used software technologies including Stratum Commerce, Velora .</p>

  <div class="abs news-photo" role="img" aria-label="Businessman touching a market chart screen" style="left:86px;top:996px;background:linear-gradient(135deg,#1d4f86,#5d93c4 55%,#2a3d5c)"></div>
  <h4 class="news-kicker" style="left:215px;top:998px">LOREM IPSUM DOLORE</h4>
  <h5 class="news-sub" style="left:216px;top:1011px">Lorem ipsum dolor sit amet</h5>
  <p class="news-text" style="left:216px;top:1025px">Sed ut perspiciatis unde omnis iste natus error sit voluptatem accusantium doloremque laudantium, totam rem aperiam, eaque ipsa quae ab illo inve-neos qui ratione voluptatem sequi nesciunt</p>
  <div class="more" style="left:217px;top:1086px">MORE</div>

  <div class="abs vdiv"></div>

  <div class="abs news-photo" role="img" aria-label="Coin stacks in front of a stock ticker board" style="left:408px;top:996px;background:linear-gradient(160deg,#0d1a33,#2b4e7a 50%,#c9a663)"></div>
  <h4 class="news-kicker" style="left:537px;top:998px">LOREM IPSUM DOLORE</h4>
  <h5 class="news-sub" style="left:538px;top:1011px">Lorem ipsum dolor sit amet</h5>
  <p class="news-text" style="left:538px;top:1025px">Sed ut perspiciatis unde omnis iste natus error sit voluptatem accusantium doloremque laudantium, totam rem aperiam, eaque ipsa quae ab illo inve-neos qui ratione voluptatem sequi nesciunt</p>
  <div class="more" style="left:538px;top:1086px">MORE</div>
</section>

<footer class="abs footer">
  <div class="footer-links"><span>Home</span><span class="sep">|</span><span>About Us</span><span class="sep">|</span><span>Portfolio</span><span class="sep">|</span><span>Contact</span></div>
  <div class="copyright">©Copy Rights 2014- Tavel Corporation. All Right Reserved</div>
</footer>
</body>
</html>
```